BrightLoop needs a Monthly Newsletter

We need a newsletter design for a company located in Sydney Australia. We are an IT Services and Software Development company with both arms separated as a business. We would like to see designs that follow the same elements that our website has being www.brightloop.com.au.
It needs an element of our corporate blue logo in it and would like the same colour elements included throughout the file.
The file needs to be MailChimp compatible and we would need all the files being HTML, the graphics, the PSD files, the MailChimp ready file, etc.

Industry/Entity Type

Graphic Design

```html
<!DOCTYPE html>
<html lang="en">
<head>
<meta charset="utf-8">
<title>BrightLoop Monthly Newsletter</title>
<link href="https://fonts.googleapis.com/css2?family=ABeeZee&family=Open+Sans:wght@400;600;700&display=swap" rel="stylesheet">
<style>
:root{
  --page:#eeeeee;
  --card:#ffffff;
  --line:#dddddd;
  --ink:#3d3d3d;
  --muted:#777777;
  --blue:#3a87e3;
  --red:#d8352b;
  --yellow:#f9b800;
  --green:#5cbf16;
  --orange:#e5482f;
  --photo-a:#9fb8cc;
  --photo-b:#4b6a86;
}
*{margin:0;padding:0;box-sizing:border-box}
html,body{width:1200px;height:3646px;overflow:hidden}
body{background:var(--page);font-family:"Open Sans",Arial,sans-serif;color:var(--ink);position:relative}
.abs{position:absolute}
.preheader{top:10px;left:0;width:1200px;text-align:center;font-size:19px;color:var(--muted)}
.preheader u{color:var(--muted)}
.card{left:49px;top:46px;width:1102px;height:3569px;background:var(--card);border:2px solid #d6d6d6;border-radius:8px;box-shadow:0 4px 14px rgba(0,0,0,.12)}
.logo{top:110px;left:0;width:1200px;display:flex;justify-content:center;align-items:center;gap:26px}
.logo-mark{width:112px;height:112px;border-radius:50%;background:var(--blue)}
.logo-name{font-family:"ABeeZee",Arial,sans-serif;font-size:86px;color:var(--blue);letter-spacing:1px}
.rule{left:97px;width:1006px;height:2px;background:var(--line)}
.nav{top:308px;left:97px;width:1006px;display:flex;justify-content:space-between;font-size:23px;color:#555;letter-spacing:.3px}
.banner{top:404px;left:97px;width:1006px;height:158px;background:var(--blue);color:#fff;display:flex;align-items:center;justify-content:space-between;padding:0 24px}
.banner p{font-family:"ABeeZee",Arial,sans-serif;font-size:30px;line-height:44px;text-align:center;flex:1;white-space:nowrap}
.ring{width:86px;height:86px;border-radius:50%;background:#fff;display:flex;align-items:center;justify-content:center;flex:none}
.photo{border-radius:2px}
.hero{top:617px;left:97px;width:1006px;height:613px;background:linear-gradient(135deg,#d9e6ef 0%,var(--photo-a) 45%,var(--photo-b) 100%);box-shadow:0 6px 12px rgba(0,0,0,.25)}
.btn{display:flex;align-items:center;justify-content:center;gap:10px;color:#fff;font-weight:700;font-size:33px;letter-spacing:.5px;border-radius:5px}
.btn svg{width:14px;height:20px}
.btn-red{background:var(--red)}
.btn-blue{background:var(--blue)}
.icon{width:82px;height:82px;border-radius:50%;background:var(--blue);display:flex;align-items:center;justify-content:center}
.title{font-family:"ABeeZee",Arial,sans-serif;font-size:45px;color:var(--ink)}
.copy{font-size:27px;line-height:38px;color:var(--ink)}
.copy-tight{font-size:26px;line-height:36px}
.tip{color:#fff;text-align:center}
.tip-inner{position:absolute;inset:20px;border:3px dashed #fff;padding:20px 20px}
.tip h3{font-size:30px;line-height:40px;font-weight:700;letter-spacing:1px}
.tip svg{display:block;margin:10px auto 10px}
.tip p{font-size:20px;line-height:25px}
.social{display:flex;gap:14px}
.social span{width:74px;height:74px;border-radius:50%}
.tile{top:3150px;width:237px;height:235px;color:#fff;display:flex;flex-direction:column;align-items:center;justify-content:flex-end;padding-bottom:24px;font-weight:700;font-size:32px;line-height:36px;text-align:center}
.tile svg{margin-bottom:auto;margin-top:26px}
.footer{top:3403px;left:97px;width:1006px;height:176px;background:var(--blue);color:#fff;font-size:27px;line-height:40px;text-align:center;display:flex;align-items:center;justify-content:center}
.footer u{color:#fff}
</style>
</head>
<body>
<p class="abs preheader">If you're having trouble viewing this email, you can view it in your <u>browser here</u></p>

<div class="abs card"></div>

<div class="abs logo">
  <span class="logo-mark"></span>
  <span class="logo-name">BrightLoop</span>
</div>

<div class="abs rule" style="top:289px"></div>
<nav class="abs nav">
  <span>IT SERVICES</span><span>MANAGED SERVICES</span><span>CLOUD</span><span>HELP ME DECIDE</span><span>ABOUT US</span><span>CONTACT US</span>
</nav>
<div class="abs rule" style="top:371px"></div>

<section class="abs banner">
  <span class="ring"><svg width="52" height="46" viewBox="0 0 52 46"><rect x="3" y="3" width="46" height="30" rx="3" fill="none" stroke="#3a87e3" stroke-width="4"/><path d="M16 18l7 7 13-13" fill="none" stroke="#3a87e3" stroke-width="4"/><path d="M18 43h16M26 33v10" stroke="#3a87e3" stroke-width="4"/></svg></span>
  <p>BrightLoop provides highly effective IT solutions<br>and services, with an agile and nimble approach</p>
  <span class="ring"><svg width="50" height="50" viewBox="0 0 50 50"><circle cx="22" cy="16" r="10" fill="#3a87e3"/><path d="M4 46c0-12 8-18 18-18s18 6 18 18z" fill="#3a87e3"/><circle cx="38" cy="38" r="9" fill="#fff" stroke="#3a87e3" stroke-width="3"/><path d="M34 38l3 3 5-6" fill="none" stroke="#3a87e3" stroke-width="3"/></svg></span>
</section>
<div class="abs rule" style="top:586px"></div>

<div class="abs photo hero" role="img" aria-label="Hands at a keyboard and mouse beneath a floating holographic data dashboard"></div>
<a class="abs btn btn-blue" style="top:1115px;left:799px;width:258px;height:79px">READ MORE <svg viewBox="0 0 14 20"><path d="M2 2l10 8-10 8z" fill="#fff"/></svg></a>

<div class="abs icon" style="top:1264px;left:97px"><svg width="50" height="50" viewBox="0 0 50 50"><g fill="#fff"><circle cx="25" cy="25" r="15"/><rect x="21" y="2" width="8" height="46" rx="2"/><rect x="2" y="21" width="46" height="8" rx="2"/><rect x="21" y="2" width="8" height="46" rx="2" transform="rotate(45 25 25)"/><rect x="21" y="2" width="8" height="46" rx="2" transform="rotate(-45 25 25)"/></g><circle cx="25" cy="25" r="7" fill="#3a87e3"/></svg></div>
<h2 class="abs title" style="top:1275px;left:204px">New Technologies</h2>
<p class="abs copy" style="top:1356px;left:97px;width:580px">Lorem ipsum dolor sit amet, consectetur adipiscing elit. Vestibulum elit erat, dapibus in laoreet in, laoreet nec purus. Vivamus lacinia velit vitae eros tincidunt vestibulum.</p>
<a class="abs btn btn-red" style="top:1516px;left:97px;width:261px;height:76px">READ MORE <svg viewBox="0 0 14 20"><path d="M2 2l10 8-10 8z" fill="#fff"/></svg></a>
<div class="abs photo" style="top:1267px;left:696px;width:404px;height:325px;background:linear-gradient(160deg,#5d6f80,#1f2a36)" role="img" aria-label="Person touching a glowing network of connected contact icons at night"></div>
<div class="abs rule" style="top:1625px"></div>

<section class="abs tip" style="top:1653px;left:97px;width:568px;height:340px;background:var(--yellow)">
  <div class="tip-inner">
    <h3>MONTHLY TECH TIP!</h3>
    <svg width="380" height="66" viewBox="0 0 380 70"><g fill="none" stroke="#3d3d3d" stroke-width="4"><rect x="14" y="8" width="50" height="36" rx="2"/><path d="M39 44v12M26 60h26"/><rect x="124" y="12" width="50" height="32" rx="2"/><path d="M114 52h70"/><rect x="232" y="6" width="40" height="54" rx="4"/><rect x="336" y="4" width="26" height="58" rx="4"/></g></svg>
    <p>Why is Managed Backup so important? Any business that values their data, understands that technology and data are at the forefront of business progression...</p>
  </div>
</section>
<section class="abs tip" style="top:1653px;left:696px;width:404px;height:340px;background:var(--green)">
  <div class="tip-inner">
    <h3>DID YOU KNOW?!</h3>
    <svg width="74" height="62" viewBox="0 0 80 70"><g fill="none" stroke="#fff" stroke-width="4"><path d="M28 40c-8-6-10-14-6-22 4-8 20-10 28-2 8 8 4 18-2 24v8H30z"/><path d="M32 56h16M34 64h12"/><path d="M4 30h10M66 30h10M10 8l8 7M70 8l-8 7"/></g></svg>
    <p>What is meant by Migration? The migration process is simple. It is the relocation of all your data to another environment.</p>
  </div>
</section>
<div class="abs rule" style="top:2017px"></div>

<div class="abs icon" style="top:2042px;left:97px"><svg width="50" height="44" viewBox="0 0 50 44"><path d="M3 6c8-3 15-3 22 2v34c-7-5-14-5-22-2z M47 6c-8-3-15-3-22 2v34c7-5 14-5 22-2z" fill="#fff"/><path d="M9 16h10M9 23h10M31 16h10M31 23h10" stroke="#3a87e3" stroke-width="3"/></svg></div>
<h2 class="abs title" style="top:2053px;left:200px">News</h2>
<p class="abs copy" style="top:2140px;left:97px;width:580px">Lorem ipsum dolor sit amet, consectetur adipiscing elit. Vestibulum elit erat, dapibus in laoreet in, laoreet nec purus. Vivamus lacinia velit vitae eros tincidunt vestibulum...</p>
<a class="abs btn btn-red" style="top:2300px;left:97px;width:261px;height:76px">READ MORE <svg viewBox="0 0 14 20"><path d="M2 2l10 8-10 8z" fill="#fff"/></svg></a>
<div class="abs photo" style="top:2054px;left:696px;width:404px;height:319px;background:linear-gradient(150deg,#6a6e73,#2a2c30 55%,#b9474a 100%)" role="img" aria-label="Close-up of a dark keyboard with a red access key"></div>
<div class="abs rule" style="top:2409px"></div>

<div class="abs icon" style="top:2437px;left:97px"><svg width="50" height="46" viewBox="0 0 50 46"><path d="M25 4c12 0 21 7 21 16s-9 16-21 16c-3 0-5 0-8-1l-11 7 3-10c-3-3-5-7-5-12C4 11 13 4 25 4z" fill="#fff"/><path d="M15 18h20M15 25h14" stroke="#3a87e3" stroke-width="3"/></svg></div>
<h2 class="abs title" style="top:2450px;left:204px">Case Studies</h2>
<div class="abs social" style="top:2440px;left:835px"><span style="background:#3b5d9f"></span><span style="background:#2aa3e0"></span><span style="background:#d8452f"></span></div>
<p class="abs copy copy-tight" style="top:2532px;left:97px;width:1006px">Lorem ipsum dolor sit amet, consectetur adipiscing elit. Vestibulum elit erat, dapibus in laoreet in, laoreet nec purus. Vivamus lacinia velit vitae eros tincidunt vestibulum. Aliquam nec ornare sem. Ut at lacus nondiam sodales ultricies.</p>
<p class="abs copy copy-tight" style="top:2686px;left:97px;width:730px">Quisque vulputate faucibus eros sit amet volutpat. Duis venenatis, orci et interdum facilisis...</p>
<a class="abs btn btn-red" style="top:2684px;left:842px;width:258px;height:76px">READ MORE <svg viewBox="0 0 14 20"><path d="M2 2l10 8-10 8z" fill="#fff"/></svg></a>
<div class="abs rule" style="top:2795px"></div>

<div class="abs icon" style="top:2825px;left:97px"><svg width="56" height="30" viewBox="0 0 56 30"><path d="M28 8c-4-6-12-6-16 0-3 5-7 7-12 4 2 9 12 14 20 10 4-2 6-6 8-8 2 2 4 6 8 8 8 4 18-1 20-10-5 3-9 1-12-4-4-6-12-6-16 0z" fill="#fff"/></svg></div>
<h2 class="abs title" style="top:2836px;left:204px">Our April Campaign</h2>
<p class="abs copy" style="top:2922px;left:97px;width:580px">Lorem ipsum dolor sit amet, consectetur adipiscing elit. Vestibulum elit erat, dapibus in laoreet in, laoreet nec purus.</p>
<svg class="abs" style="top:3048px;left:97px" width="212" height="42" viewBox="0 0 212 42"><defs><path id="star" d="M20 2l5.3 12.4 13.4 1.1-10.2 8.8 3.1 13.1L20 30.4 8.4 37.4l3.1-13.1L1.3 15.5l13.4-1.1z" fill="#f9b800"/></defs><use href="#star"/><use href="#star" x="42"/><use href="#star" x="84"/><use href="#star" x="126"/><use href="#star" x="168"/></svg>
<div class="abs photo" style="top:2838px;left:699px;width:398px;height:243px;background:linear-gradient(120deg,#f1f1ef,#d7d9da 60%,#e6c34a 100%)" role="img" aria-label="Smiling woman working on a laptop in a bright office"></div>
<div class="abs rule" style="top:3123px"></div>

<div class="abs tile" style="left:97px;background:var(--yellow)">
  <svg width="110" height="90" viewBox="0 0 110 90"><g fill="#fff"><circle cx="55" cy="22" r="16"/><path d="M27 80c0-22 12-34 28-34s28 12 28 34z"/><circle cx="20" cy="32" r="12"/><path d="M0 78c0-16 8-26 20-26 5 0 8 1 11 3-6 7-8 14-8 23z"/><circle cx="90" cy="32" r="12"/><path d="M110 78c0-16-8-26-20-26-5 0-8 1-11 3 6 7 8 14 8 23z"/></g></svg>
  IT SERVICES
</div>
<div class="abs tile" style="left:352px;background:var(--blue)">
  <svg width="100" height="80" viewBox="0 0 100 80"><g fill="#fff"><rect x="38" y="2" width="24" height="20"/><rect x="4" y="56" width="24" height="20"/><rect x="38" y="56" width="24" height="20"/><rect x="72" y="56" width="24" height="20"/></g><path d="M50 22v34M16 56V40h68v16" fill="none" stroke="#fff" stroke-width="5"/></svg>
  MANAGED<br>SERVICES
</div>
<div class="abs tile" style="left:608px;background:var(--green)">
  <svg width="120" height="80" viewBox="0 0 120 80"><path d="M26 76C12 76 4 66 4 56s8-20 20-20c2-16 16-28 34-28 16 0 28 10 32 24 14 0 26 10 26 22s-10 22-24 22z" fill="#fff"/></svg>
  CLOUD
</div>
<div class="abs tile" style="left:863px;background:var(--orange)">
  <svg width="96" height="96" viewBox="0 0 96 96"><circle cx="48" cy="48" r="46" fill="#fff"/><path d="M34 38c0-9 6-15 14-15s14 5 14 13c0 10-12 11-12 21" fill="none" stroke="#e5482f" stroke-width="9" stroke-linecap="round"/><circle cx="50" cy="72" r="6" fill="#e5482f"/></svg>
  HELP ME<br>DECIDE
</div>

<footer class="abs footer"><p>You are receiving this email because you subscribed to our newsletter.<br><u>Unsubscribe</u> or change your preferences here.</p></footer>
</body>
</html>
```